Business Card for a New Zealand IT Startup

I need a business card for VELTA Holdings. We are a young startup based in New Zealand working in internet marketing and web development. The design should have some element connected to New Zealand, such as wave, koru or silver fern, just don't use a kiwi bird.

```html
<!DOCTYPE html>
<html lang="en">
<head>
<meta charset="utf-8">
<title>VELTA Holdings – Business Card</title>
<link rel="stylesheet" href="https://fonts.googleapis.com/css2?family=Source+Sans+3:ital,wght@0,400;0,600;0,700;1,400&display=swap">
<style>
  :root {
    --page: #e9e7e4;
    --card-front: #1f2124;
    --card-back: #17181a;
    --blue: #1f7fcf;
    --orange: #ee5a2a;
    --white: #f4f4f4;
    --rule: #d9d9d9;
    --emboss: #2b2d30;
    --emboss-text: #3a3d41;
    --wave-faint: #25272b;
    --back-text: #c9c9c9;
  }
  * { box-sizing: border-box; margin: 0; padding: 0; }
  html, body { width: 1200px; height: 864px; overflow: hidden; }
  body {
    background: var(--page);
    font-family: "Source Sans 3", "Myriad Pro", sans-serif;
    display: flex; flex-direction: column; align-items: center; justify-content: center;
    gap: 40px;
  }
  .card {
    position: relative; width: 640px; height: 366px; overflow: hidden;
    border-radius: 4px; box-shadow: 0 6px 18px rgba(0,0,0,.18);
  }

  /* back */
  .card-back { background: var(--card-back); }
  .back-waves { position: absolute; left: 0; bottom: 0; width: 100%; height: 120px; }
  .back-mark {
    position: absolute; left: 50%; top: 130px; transform: translate(-50%, -50%);
    display: flex; align-items: center; gap: 18px; white-space: nowrap;
  }
  .back-mark .dot {
    width: 110px; height: 110px; border-radius: 50%; background: var(--emboss);
    box-shadow: inset 0 2px 3px rgba(255,255,255,.06), inset 0 -3px 6px rgba(0,0,0,.5);
  }
  .back-mark .name { color: var(--emboss-text); font-weight: 700; font-size: 34px; letter-spacing: 1px; }
  .back-url {
    position: absolute; left: 0; right: 0; top: 236px; text-align: center;
    color: var(--back-text); font-size: 16px; letter-spacing: 7px;
  }

  /* front */
  .card-front { background: var(--card-front); color: var(--white); }
  .person { position: absolute; left: 36px; top: 74px; white-space: nowrap; }
  .person-name { color: var(--blue); font-weight: 700; font-size: 30px; line-height: 1; letter-spacing: .5px; }
  .person-title { color: var(--orange); font-size: 17px; margin-top: 2px; letter-spacing: .5px; }
  .divider { position: absolute; left: 36px; right: 34px; top: 150px; height: 1.5px; background: var(--rule); }
  .contacts { position: absolute; left: 36px; top: 166px; list-style: none; font-size: 16px; line-height: 22px; }
  .contacts li { display: flex; align-items: center; gap: 9px; }
  .contacts svg { width: 14px; height: 14px; fill: var(--blue); flex: none; }
  .brand { position: absolute; right: 36px; top: 62px; display: flex; align-items: center; gap: 12px; white-space: nowrap; }
  .brand .name { color: var(--blue); font-weight: 700; font-size: 40px; line-height: 1; letter-spacing: 1px; }
  .brand .dot { width: 34px; height: 34px; border-radius: 50%; background: var(--blue); }
  .address { position: absolute; right: 36px; top: 166px; text-align: right; font-size: 17px; line-height: 22px; }
  .wave-band { position: absolute; left: 0; bottom: 0; width: 100%; height: 96px; }
  .band-url { position: absolute; right: 36px; bottom: 0; line-height: 54px; color: var(--white); font-size: 18px; }
</style>
</head>
<body>

<section class="card card-back" aria-label="Business card back">
  <svg class="back-waves" viewBox="0 0 640 120" preserveAspectRatio="none" aria-hidden="true">
    <path d="M0 70 C80 40 160 40 240 70 S400 100 480 70 S600 40 640 55 L640 120 L0 120 Z" fill="var(--wave-faint)"/>
    <path d="M0 92 C90 66 170 66 260 92 S420 118 510 92 S610 70 640 80" fill="none" stroke="var(--emboss)" stroke-width="2"/>
  </svg>
  <div class="back-mark">
    <span class="dot"></span>
    <span class="name">VELTA Holdings</span>
  </div>
  <p class="back-url">www.veltaholdings.com</p>
</section>

<section class="card card-front" aria-label="Business card front">
  <div class="person">
    <p class="person-name">MARA QUINN</p>
    <p class="person-title">PRESIDENT</p>
  </div>

  <div class="brand">
    <span class="name">VELTA Holdings</span>
    <span class="dot"></span>
  </div>

  <div class="divider"></div>

  <ul class="contacts">
    <li><svg viewBox="0 0 16 16" aria-hidden="true"><path d="M3 1.5l3 .5 1 3.5-1.8 1.2a9 9 0 0 0 4.1 4.1L10.5 9l3.5 1 .5 3-2 1.5C6.5 14.5 1.5 9.5 1.5 3.5z"/></svg>021 448 7306</li>
    <li><svg viewBox="0 0 16 16" aria-hidden="true"><path d="M4.5 0.5h7a1 1 0 0 1 1 1v13a1 1 0 0 1-1 1h-7a1 1 0 0 1-1-1v-13a1 1 0 0 1 1-1zM5 2.5v9.5h6V2.5zM8 13a.8.8 0 1 0 0 1.6A.8.8 0 0 0 8 13z"/></svg>022 519 6842</li>
    <li><svg viewBox="0 0 16 16" aria-hidden="true"><path d="M4 1h8v4H4zM1.5 6h13a1 1 0 0 1 1 1v5h-3v3h-9v-3h-3V7a1 1 0 0 1 1-1zM5 10v3.5h6V10z"/></svg>09 377 1254</li>
    <li><svg viewBox="0 0 16 16" aria-hidden="true"><path d="M1 3h14v10H1zM2.5 4.5v.4L8 9l5.5-4.1v-.4z"/></svg>mara@veltaholdings.com</li>
  </ul>

  <p class="address">27 Harbour View Road<br>Wellington 6011, NZ</p>

  <svg class="wave-band" viewBox="0 0 640 96" preserveAspectRatio="none" aria-hidden="true">
    <path d="M180 58 C250 30 320 30 390 48 S520 64 640 36" fill="none" stroke="var(--blue)" stroke-width="2"/>
    <path d="M250 96 C300 70 340 44 400 42 S520 56 640 42 L640 96 Z" fill="var(--orange)"/>
  </svg>
  <span class="band-url">www.veltaholdings.com</span>
</section>

</body>
</html>
```